Elegant Business Card for Technology Company

Client is a supplier of innovative industrial communications and automation equipment since 2002. This contest is to gather fresh ideas for a redesign of the existing business card. Client is looking for design that best communicates tagline "Industrial Networking and Computing Specialist".

Design submissions should look modern, clean, elegant and professional. It should not be cluttered. Use white as the primary colour. Orange and black as secondary colour. Refer to jpeg File 1 on the current design.

Fonts used by Client used include Arial Regular, Arial Black, Roboto Regular, Roboto Black and Lato.

The winning design will be sent for offset printing using super white 250gsm artcard paper (open for suggestions).

Target Market(s)

System Engineers, Project Managers, Purchasing Managers from companies providing engineering services for Smart Cities.

Industry/Entity Type

Information Technology

Contact Information for Business Card

Refer to PDF File 3 for Business Card Details. Priority of short contact information would be as follows Name > Job Title > Email > Mobile > Web > Tel > Fax > Business Address >UEN (UEN represents company registration number)

Font styles to use
Sans Serif

Colors
ffffff
f37122
000000
5c5c5c

Requirements
Must have
• Refer to AI File 2 (Company Logo) & PDF File 3 (Information on Namecard)
Should not have
• No QR codes
• No Social Media Icons
• Do not create full Black or Orange colour background

```html
<!DOCTYPE html>
<html lang="en">
<head>
<meta charset="utf-8">
<title>Veltrix Business Card</title>
<link href="https://fonts.googleapis.com/css2?family=Lato:wght@400;700;900&display=swap" rel="stylesheet">
<style>
  :root{
    --white:#ffffff;
    --orange:#f37122;
    --orange-deep:#e0651c;
    --black:#111111;
    --grey:#5c5c5c;
    --stage:#e9e7e3;
  }
  *{box-sizing:border-box;margin:0;padding:0}
  html,body{width:1200px;height:780px;overflow:hidden}
  body{background:var(--stage);font-family:'Lato',Arial,sans-serif;color:var(--black);position:relative}
  .card{position:absolute;top:230px;width:540px;height:310px;background:var(--white);
    box-shadow:0 6px 18px rgba(0,0,0,.15);overflow:hidden}
  .card--front{left:40px}
  .card--back{left:620px}

  /* front */
  .front-band{position:absolute;left:0;right:0;bottom:0;height:12px;
    background:linear-gradient(90deg,var(--orange-deep),var(--orange),#f5a03a)}
  .brand{position:absolute;left:26px;top:118px;display:flex;align-items:center;gap:10px}
  .brand__dot{width:54px;height:54px;border-radius:50%;background:var(--orange)}
  .brand__name{font-weight:900;font-size:34px;letter-spacing:1px;color:var(--black)}
  .company{position:absolute;left:160px;top:90px;font-size:15px;color:var(--black)}
  .web--front{position:absolute;right:28px;top:22px;font-size:12px;color:var(--orange)}
  .person{position:absolute;right:28px;top:56px;text-align:right}
  .person__name{font-weight:700;font-size:21px;color:var(--black)}
  .person__title{font-size:12px;color:var(--orange);margin-top:2px}
  .divider{position:absolute;left:160px;right:28px;top:118px;height:1px;background:var(--orange)}
  .details{position:absolute;right:28px;top:134px;text-align:right;font-size:12px;line-height:1.55;color:var(--black)}
  .details__uen{color:var(--orange)}
  .contacts{position:absolute;left:26px;bottom:36px;list-style:none;font-size:12.5px;line-height:1.6;color:var(--black)}
  .contacts li{display:flex;align-items:center;gap:8px}
  .contacts svg{width:13px;height:13px;flex:none}

  /* back */
  .back-band{position:absolute;left:0;top:0;bottom:0;width:12px;
    background:linear-gradient(180deg,var(--orange),var(--orange-deep))}
  .back-texture{position:absolute;right:0;top:0;width:62%;height:100%;
    background:radial-gradient(ellipse at 70% 45%,rgba(243,113,34,.07),rgba(243,113,34,0) 70%)}
  .brand--back{left:auto;right:44px;top:58px}
  .tagline{position:absolute;left:40px;right:40px;top:140px;font-size:16px;color:var(--black)}
  .dotline{position:absolute;left:40px;right:40px;top:168px;border-top:1.5px dotted var(--orange)}
  .services{position:absolute;left:40px;top:180px;list-style:none;font-size:12.5px;line-height:1.55;color:var(--black)}
  .web--back{position:absolute;left:40px;bottom:16px;font-size:12px;color:var(--black)}
</style>
</head>
<body>

<section class="card card--front">
  <p class="web--front">www.veltrix.com</p>
  <div class="person">
    <p class="person__name">Daniel Loh</p>
    <p class="person__title">Sales Manager</p>
  </div>
  <div class="brand">
    <span class="brand__dot"></span>
    <span class="brand__name">VELTRIX</span>
  </div>
  <p class="company" style="top:92px">Veltrix Asia Pacific Pte Ltd</p>
  <div class="divider"></div>
  <div class="details">
    <p class="details__uen">UEN No <span style="color:var(--black)">201104417</span></p>
    <p>22 Kallang Link Tech Hub</p>
    <p>#04-12 (Block B), Singapore 349871</p>
  </div>
  <ul class="contacts">
    <li><svg viewBox="0 0 13 13"><rect width="13" height="13" rx="2" fill="var(--orange)"/><rect x="4" y="2.5" width="5" height="8" rx="1" fill="#fff"/></svg>+65 9123 4567</li>
    <li><svg viewBox="0 0 13 13"><rect width="13" height="13" rx="2" fill="var(--orange)"/><path d="M3.5 3.5c0 3.5 2.5 6 6 6l.8-1.6-1.8-.9-.8.8c-1-.5-1.6-1.1-2-2l.8-.8-.9-1.8z" fill="#fff"/></svg>+65 6234 5810</li>
    <li><svg viewBox="0 0 13 13"><rect width="13" height="13" rx="2" fill="var(--orange)"/><rect x="3" y="5" width="7" height="5" fill="#fff"/><rect x="4.5" y="2.5" width="4" height="2" fill="#fff"/></svg>+65 6234 5811</li>
    <li><svg viewBox="0 0 13 13"><rect width="13" height="13" rx="2" fill="var(--orange)"/><rect x="2.5" y="4" width="8" height="5.5" fill="#fff"/><path d="M2.5 4l4 3 4-3" stroke="var(--orange)" stroke-width=".9" fill="none"/></svg>sales@veltrix.com.sg</li>
  </ul>
  <div class="front-band"></div>
</section>

<section class="card card--back">
  <div class="back-band"></div>
  <div class="back-texture" role="img" aria-label="Faint orange dot pattern background"></div>
  <div class="brand brand--back">
    <span class="brand__dot"></span>
    <span class="brand__name">VELTRIX</span>
  </div>
  <p class="tagline">Industrial Networking and Computing Specialist</p>
  <div class="dotline"></div>
  <ul class="services">
    <li>Industrial Ethernet / Wireless / Cellular</li>
    <li>Industrial and Emedded Computing</li>
    <li>Serial / Fieldbus Connectivity</li>
    <li>IP Video Surveillance</li>
    <li>Remote Automation</li>
  </ul>
  <p class="web--back">www.veltrix.com</p>
</section>

</body>
</html>
```